Quiet Harbor Prints gallery website

I need a Website for a gallery with a shopify integration or maybe even better also compatible with squarespace.
the website should have following riders: Künstler, Veranstaltungen, Shop, About Us.
some nice examples for inspiration of the website architecture are:
https://www.lindwerkraum.com/
https://www.plattenbau-salon.com/de/
https://moorlichtraum.de/
It should be easy for us to make adaptations and fill the website with new content.
Attached there is the CI an logo for the brand.
Target Market(s)
Art Collectors,
Industry/Entity Type
artgallery
Coding
Coded - Design and coding required
Number of Pages Required
3 page
Font styles to use
Look and feel

```html
<!DOCTYPE html>
<html lang="en">
<head>
<meta charset="UTF-8">
<title>Quiet Harbor Prints – Gallery</title>
<link rel="stylesheet" href="https://fonts.googleapis.com/css2?family=Forum&family=Josefin+Sans:wght@300;400&family=DM+Sans:wght@400;500&display=swap">
<style>
  :root {
    --header-bg: #f5f8fb;
    --ink: #1d1d1f;
    --muted: #6b6b6f;
    --accent: #c12a38;
    --hero-light: #f4f4f3;
    --hero-mid: #e3e3e1;
    --hero-dark: #cfcfcc;
    --white: #ffffff;
  }
  * { box-sizing: border-box; margin: 0; padding: 0; }
  html, body {
    width: 1200px;
    height: 674px;
    overflow: hidden;
    background: var(--white);
  }
  .page {
    position: relative;
    width: 1200px;
    height: 674px;
  }
  .site-header {
    position: absolute;
    top: 0; left: 0;
    width: 1200px;
    height: 123px;
    background: var(--header-bg);
  }
  .brand {
    position: absolute;
    left: 34px;
    top: 60px;
    font-family: "Josefin Sans", sans-serif;
    font-weight: 300;
    font-size: 18px;
    line-height: 20px;
    color: var(--ink);
    text-decoration: none;
    white-space: nowrap;
  }
  .main-nav a {
    position: absolute;
    top: 60px;
    font-family: "Josefin Sans", sans-serif;
    font-weight: 300;
    font-size: 19px;
    line-height: 20px;
    color: var(--ink);
    text-decoration: none;
    white-space: nowrap;
  }
  .main-nav a.is-active { color: var(--accent); }
  .nav-home { left: 417px; }
  .nav-events { left: 510px; }
  .nav-gallery { left: 605px; }
  .nav-shop { left: 702px; }
  .nav-contact { left: 785px; }
  .sign-in {
    position: absolute;
    top: 60px;
    left: 1050px;
    display: flex;
    align-items: center;
    gap: 12px;
    font-family: "Josefin Sans", sans-serif;
    font-weight: 300;
    font-size: 19px;
    line-height: 20px;
    color: var(--ink);
    text-decoration: none;
  }
  .hero {
    position: absolute;
    top: 123px;
    left: 0;
    width: 1200px;
    height: 539px;
  }
  .hero-photo {
    position: absolute;
    inset: 0;
    background:
      linear-gradient(90deg, var(--hero-dark) 0%, var(--hero-mid) 10%, var(--hero-light) 30%, var(--hero-light) 70%, var(--hero-mid) 90%, var(--hero-dark) 100%);
  }
  .hero-photo::after {
    content: "";
    position: absolute;
    inset: 0;
    background: linear-gradient(180deg, rgba(255,255,255,0.35) 0%, rgba(255,255,255,0.1) 50%, rgba(255,255,255,0.55) 100%);
  }
  .hero-content {
    position: absolute;
    top: 177px;
    left: 0;
    width: 1200px;
    text-align: center;
  }
  .hero-title {
    font-family: "Forum", serif;
    font-weight: 400;
    font-size: 54px;
    line-height: 50px;
    color: var(--ink);
    letter-spacing: -0.4px;
  }
  .hero-lead {
    margin: 28px auto 0;
    width: 560px;
    font-family: "DM Sans", sans-serif;
    font-size: 15px;
    line-height: 21px;
    color: var(--muted);
  }
  .hero-cta {
    position: absolute;
    left: 513px;
    top: 377px;
    width: 173px;
    height: 42px;
    background: var(--accent);
    color: var(--white);
    display: flex;
    align-items: center;
    padding-left: 31px;
    gap: 36px;
    font-family: "DM Sans", sans-serif;
    font-weight: 500;
    font-size: 15px;
    letter-spacing: 0.5px;
    text-decoration: none;
  }
</style>
</head>
<body>
<div class="page">
  <header class="site-header">
    <a class="brand" href="#">Quiet Harbor Prints</a>
    <nav class="main-nav">
      <a class="nav-home is-active" href="#">Home</a>
      <a class="nav-events" href="#">Events</a>
      <a class="nav-gallery" href="#">Gallery</a>
      <a class="nav-shop" href="#">Shop</a>
      <a class="nav-contact" href="#">Contact</a>
    </nav>
    <a class="sign-in" href="#">
      <svg width="15" height="15" viewBox="0 0 16 16" aria-hidden="true">
        <circle cx="6.5" cy="6.5" r="4.8" fill="none" stroke="#1d1d1f" stroke-width="1.5"/>
        <line x1="10" y1="10" x2="14.5" y2="14.5" stroke="#1d1d1f" stroke-width="1.7" stroke-linecap="round"/>
      </svg>
      <span>Sign in</span>
    </a>
  </header>

  <section class="hero">
    <div class="hero-photo" role="img" aria-label="Bright white gallery hall with framed artworks on the walls and a glossy floor"></div>
    <div class="hero-content">
      <h1 class="hero-title">Discover Fine Art Masterpieces at<br>Quiet Harbor Prints Gallery</h1>
      <p class="hero-lead">Embark on a journey through timeless beauty and artistic excellence at Quiet Harbor Prints Gallery. Explore our curated collection of exquisite masterpieces.</p>
    </div>
    <a class="hero-cta" href="#">
      <span>SHOP</span>
      <svg width="40" height="10" viewBox="0 0 40 10" aria-hidden="true">
        <line x1="0" y1="5" x2="38" y2="5" stroke="#ffffff" stroke-width="1.2"/>
        <polyline points="33,1 38,5 33,9" fill="none" stroke="#ffffff" stroke-width="1.2"/>
      </svg>
    </a>
  </section>
</div>
</body>
</html>
```